KR Appraisals website redesign

I would like to refresh my existing website of www.krappraisals-example.com with new graphics, look and feel, as well as updated structure and wording. Content and layout changes have been uploaded to this project Brief.

My existing website has a dark feel. I am now looking for a light and energetic feel. Financial Services is my industry, so the website should be reflect that. I would also like to reflect the concepts of Trust, Service and Expertise.

The website must be serious and upmarket.

Target Market(s)

Corporate board members, CFO's, treasurers and controllers
Auditors, tax advisors, private equity and venture capital asset managers, investors, tax authorities

Industry/Entity Type

Financial Service

Coding

Coded - Design and coding required

Number of Pages Required

5+ page

Font styles to use
Sans Serif
Other font styles liked:
• Designer can choose another modern font

Colors
0355a3
3277b5
85acd3
eaf1f7
f37122
f68d4d
9bcb3c
acd037
cadf82

Requirements
Must have
• Good hi resolution pictures that convey "Finance", "Trust", "Service" or "Expertise".
• An anti-bot (such as Captcha) mechanism in the contact form.
Should not have
• Must not have all content on one rolling screen.

```html
<!DOCTYPE html>
<html lang="en">
<head>
<meta charset="utf-8">
<title>KR Appraisals – Our Services</title>
<link rel="stylesheet" href="https://fonts.googleapis.com/css2?family=Figtree:wght@400;500;600;700&display=swap">
<style>
:root{
  --blue:#0355a3;
  --orange:#f37122;
  --green:#9bcb3c;
  --ink:#555;
  --nav:#6b6b6b;
  --panel:#f2f2f2;
  --footer:#333;
  --footer-text:#9a9a9a;
  --rule:#5a5a5a;
}
*{margin:0;padding:0;box-sizing:border-box}
html,body{width:1200px;height:1144px;overflow:hidden;background:#fff}
body{font-family:"Figtree",sans-serif;position:relative;color:var(--ink)}

.site-header{position:absolute;left:0;top:0;width:1200px;height:100px;
  background:linear-gradient(90deg,#e4e4dc 0%,#ecede0 50%,#f6f7e6 100%)}
.brand{position:absolute;display:flex;align-items:center;gap:10px;color:#7a7a7a;font-weight:500;font-size:24px;letter-spacing:.5px}
.brand-mark{width:16px;height:16px;background:#8a8a8a}
.site-header .brand{left:161px;top:34px}
.main-nav{position:absolute;top:45px;font-size:11.5px;font-weight:600;text-transform:uppercase}
.main-nav a{position:absolute;white-space:nowrap;color:var(--nav);text-decoration:none}
.main-nav a.active{color:var(--blue)}

.page-title{position:absolute;top:184px;left:0;width:1200px;text-align:center;
  color:var(--orange);font-size:40px;font-weight:700;letter-spacing:-.5px}

.service-panel{position:absolute;left:562px;top:281px;width:477px;height:420px;background:var(--panel)}
.service-photo{position:absolute;left:164px;top:340px;width:439px;height:292px;
  background:radial-gradient(ellipse at 65% 35%,#39b6f0 0%,#1479d6 35%,#0a3f9c 70%,#061f63 100%)}
.service-title{position:absolute;left:639px;top:386px;color:var(--green);font-size:31px;
  font-weight:600;line-height:37.5px;text-transform:uppercase}
.service-text{position:absolute;left:639px;top:486px;width:365px;font-size:11px;line-height:18.75px;color:var(--ink)}

.site-footer{position:absolute;left:0;top:791px;width:1200px;height:353px}
.site-footer svg.band{position:absolute;left:0;top:0}
.site-footer .brand{left:0;width:1200px;justify-content:center;top:59px;color:#8e8e8e}
.footer-rule{position:absolute;left:161px;width:879px;height:1px;background:var(--rule)}
.footer-nav{top:158px}
.footer-nav a{color:#8a8a8a}
.footer-nav a.active{color:var(--green)}
.footer-col{position:absolute;top:218px;font-size:11px;line-height:22.5px;color:var(--footer-text)}
.footer-col h3{color:var(--orange);font-size:14px;font-weight:600;margin-bottom:7px;line-height:18px;text-transform:uppercase}
.footer-col .hl{color:var(--green)}
.footer-col .lt{color:#eee}
.contact-line{position:relative;padding-left:20px}
.contact-line svg{position:absolute;left:0;top:4px}
.address{line-height:16px;padding-top:4px}
.phone{color:#eee;font-size:12px;margin-top:12px}
.badge{position:absolute;background:#4a4a4a}
</style>
</head>
<body>

<header class="site-header">
  <div class="brand"><span class="brand-mark"></span>KR Appraisals</div>
  <nav class="main-nav">
    <a style="left:611px">Home</a>
    <a style="left:686px">About</a>
    <a class="active" style="left:766px">Services</a>
    <a style="left:861px">News &amp; Views</a>
    <a style="left:985px">Contact</a>
  </nav>
</header>

<h1 class="page-title">OUR SERVICES</h1>

<section>
  <div class="service-panel"></div>
  <div class="service-photo" role="img" aria-label="Photo of glowing blue DNA double helix strands over a network of connected points"></div>
  <h2 class="service-title">Intellectual<br>Property Valuation</h2>
  <p class="service-text">Patents, unpatented technologies, know how, brands, trademarks, databases, customer-related assets - this is a limited sample of the wide universe of intellectual property that clients trust KR Appraisals to value. There are many techniques for valuing intellectual property and no two assets are alike. Trust KR Appraisals for our expertise and client-centric approach.</p>
</section>

<footer class="site-footer">
  <svg class="band" width="1200" height="353" viewBox="0 0 1200 353">
    <polygon points="0,68 600,0 1200,68 1200,353 0,353" fill="#333"/>
  </svg>
  <div class="brand"><span class="brand-mark"></span>KR Appraisals</div>
  <div class="footer-rule" style="top:145px"></div>
  <nav class="main-nav footer-nav">
    <a class="active" style="left:386px">Home</a>
    <a style="left:461px">About</a>
    <a style="left:541px">Services</a>
    <a style="left:636px">News &amp; Views</a>
    <a style="left:760px">Contact</a>
  </nav>
  <div class="footer-rule" style="top:190px"></div>

  <div class="footer-col" style="left:163px">
    <h3>Credits</h3>
    <div>© 2019 <span class="hl">KR Appraisals B.V.</span></div>
    <div>Logo by <span class="lt">Mira Hollander</span></div>
    <div>Website by <span class="hl">Northline Webworks</span></div>
  </div>

  <div class="footer-col" style="left:466px">
    <h3>Oostmeer</h3>
    <div class="contact-line address">
      <svg width="10" height="13" viewBox="0 0 10 13"><path d="M5 0a5 5 0 0 0-5 5c0 3.5 5 8 5 8s5-4.5 5-8a5 5 0 0 0-5-5zm0 7a2 2 0 1 1 0-4 2 2 0 0 1 0 4z" fill="#9bcb3c"/></svg>
      Havenkade 48<br>2331 AB Oostmeer
    </div>
    <div class="contact-line phone">
      <svg width="12" height="12" viewBox="0 0 12 12"><path d="M2.4 0.5 4.2 2.7 3.3 4.2c.7 1.6 2.1 3 3.6 3.7l1.5-.9 2.2 1.8-.9 2.3C5 11 1 7 .3 2.4z" fill="#9bcb3c"/></svg>
      010 555 0147
    </div>
  </div>

  <div class="badge" style="left:769px;top:259px;width:120px;height:25px;border-radius:3px" role="img" aria-label="Partner institute badge"></div>
  <div class="badge" style="left:913px;top:244px;width:122px;height:49px;border-radius:3px" role="img" aria-label="Professional appraisers society badge"></div>
</footer>

</body>
</html>
```